We need a redesign of our current website: www.halvenridgegroup.com. Halvenridge Group is a fully integrated hospitality development, management, and investment firm. We strive for leadership in each of our segments by building quality assets, exacting high standards of customer service, and focusing on returns for our investors and partners.

It is our mission to provide our guests an exceptional lodging experience; our clients an unsurpassed level of management in their properties; and create positive returns for our investors and partners. We achieve our mission via a company culture of transparency, ownership of our actions, and accountability for our results.

Target Market(s)

hotel owners, hotel developers, hotel investors, bankers

Industry/Entity Type

Hospitality

Requirements
Must have
• Our logo has to be there along with the quote and the ability to convey the following quote off of our current website: "Halvenridge was founded on the principles of integrity, honesty, loyalty, and trust. These convictions embody our company at every level, and show in every action."

```html
<!DOCTYPE html>
<html lang="en">
<head>
<meta charset="utf-8">
<title>Halvenridge Group</title>
<link rel="stylesheet" href="https://fonts.googleapis.com/css2?family=Arimo:ital,wght@0,400;0,700;1,400&family=Questrial&display=swap">
<style>
:root{
  --gold:#e0a312;
  --gold-light:#f3c236;
  --gold-dark:#a9780a;
  --gold-text:#d08f06;
  --ink:#444;
  --ink-soft:#666;
  --link-red:#9b1b12;
  --page:#ececec;
  --panel:#ffffff;
  --rule:#d8d8d8;
  --footer:#0b0b0b;
  --photo-warm-1:#7a4a2a;
  --photo-warm-2:#c79a6a;
}
*{box-sizing:border-box;margin:0;padding:0}
html,body{width:919px;height:1200px;overflow:hidden}
body{position:relative;background:var(--page);font-family:"Arimo",Arial,sans-serif;color:var(--ink);font-size:11px}
.abs{position:absolute}

/* header */
.site-header{left:0;top:0;width:919px;height:105px;background:linear-gradient(#fbfbfb,#f2f2f2);border-top:4px solid #222}
.brand{left:108px;top:22px;display:flex;align-items:center;gap:10px}
.brand-mark{width:48px;height:48px;border-radius:50%;background:var(--gold)}
.brand-name{font-family:"Questrial",sans-serif;font-size:24px;color:var(--gold-text);letter-spacing:1px;line-height:1}
.utility{left:614px;top:20px;display:flex;gap:14px;font-size:10px;color:var(--gold-dark)}
.utility span{display:flex;align-items:center;gap:5px}
.utility svg{width:16px;height:16px}
.phone{left:706px;top:44px;font-size:17px;color:var(--gold-text);display:flex;gap:5px;align-items:center}
.search{left:613px;top:70px;width:207px;height:16px;display:flex;border:1px solid #999}
.search-field{flex:1;background:linear-gradient(#cfcfcf,#e4e4e4)}
.search-btn{width:56px;background:var(--gold);font-size:10px;color:#3b2a00;text-align:center;line-height:14px}

.main-nav{left:0;top:105px;width:919px;height:31px;background:linear-gradient(var(--gold-light),var(--gold) 60%,var(--gold-dark));display:flex;padding-left:96px}
.main-nav a{color:#fff;text-decoration:none;font-size:11px;padding:0 14px;line-height:31px;border-right:1px solid rgba(255,255,255,.35)}
.main-nav a:last-child{border-right:0}

/* hero */
.hero{left:92px;top:147px;width:736px;height:229px;background:linear-gradient(100deg,var(--photo-warm-1),var(--photo-warm-2) 45%,#5a3418 70%,#b9966a)}
.hero-title{left:111px;top:178px;font-family:"Questrial",sans-serif;font-size:26px;color:#fff;letter-spacing:.5px}
.hero-text{left:112px;top:228px;width:430px;font-size:14px;line-height:19px;color:#fff}
.hero-dots{left:119px;top:339px;display:flex;gap:7px}
.hero-dots span{width:19px;height:19px;border-radius:50%;background:var(--gold);color:#fff;font-size:10px;font-weight:700;text-align:center;line-height:19px}

/* content panel */
.content-panel{left:93px;top:388px;width:735px;height:572px;background:var(--panel);border-radius:4px;box-shadow:0 2px 5px rgba(0,0,0,.25)}
.section-tab{height:32px;background:#fff;border-radius:4px;box-shadow:0 2px 4px rgba(0,0,0,.2);display:flex;align-items:center;gap:9px;padding-left:12px;font-family:"Questrial",sans-serif;font-size:13px;color:var(--gold-text)}
.tab-icon{width:16px;height:16px;border-radius:50%;background:var(--gold);flex:none}
.welcome-tab{left:113px;top:405px;width:295px}
.welcome-photo{left:112px;top:458px;width:92px;height:60px;background:linear-gradient(#8aa0b8,#5b5f68)}
.welcome-text{left:112px;top:455px;width:468px;font-size:9.4px;line-height:13.4px;color:var(--ink-soft)}
.welcome-text::before{content:"";float:left;width:98px;height:62px}
.read-more{font-style:italic;color:var(--link-red);font-size:9.5px}
.side-tab{left:641px;width:164px}
.side-text{left:649px;width:150px;font-size:9.4px;line-height:14px;color:var(--ink-soft)}
.side-text .name{color:#444}

/* tabs */
.tab-row{left:102px;top:693px;display:flex;gap:2px}
.tab-row span{height:28px;padding:0 14px;background:linear-gradient(var(--gold-light),var(--gold));color:#fff;font-size:10px;line-height:30px;border-radius:2px 2px 0 0}
.tab-row .active{background:linear-gradient(#b88a1a,var(--gold-dark))}
.tab-box{left:102px;top:721px;width:717px;height:222px;border:1px solid #ccc;background:#fff}
.tab-photo{left:222px;top:722px;width:597px;height:221px;background:linear-gradient(90deg,#ffffff 0%,#eef1f3 30%,#c9cfd6 55%,#9aa3ae 80%,#6f7580)}
.service-list{list-style:none;font-size:10px;color:var(--ink-soft)}
.service-list li{display:flex;align-items:center;gap:7px;height:22.6px}
.service-list li::before{content:"";width:7px;height:7px;border-radius:1px;background:#b0425a;flex:none}
.service-list li.plain::before{background:none}

/* footer columns */
.col-head{font-family:"Questrial",sans-serif;font-size:13px;color:var(--gold-text);display:flex;align-items:center;gap:9px}
.col-rule{top:983px;width:1px;height:140px;background:#e5c88a}
.col-title{font-size:10px;font-weight:700;line-height:14px;color:#444}
.col-body{font-size:9.5px;line-height:14px;color:var(--ink-soft)}
.more-btn{width:54px;height:18px;border-radius:4px;background:linear-gradient(var(--gold-light),var(--gold-dark));color:#fff;font-size:10px;text-align:center;line-height:18px}
.social{left:628px;top:1017px;display:flex;gap:14px}
.social span{width:31px;height:31px;border-radius:4px;background:linear-gradient(#f2f2f2,#c9c9c9);box-shadow:0 1px 2px rgba(0,0,0,.3)}
.footer-brand{left:633px;top:1076px;display:flex;align-items:center;gap:8px}
.footer-brand .brand-mark{width:34px;height:34px;background:#555}
.footer-brand .brand-name{font-size:16px;color:#555}

.site-footer{left:0;top:1142px;width:919px;height:58px;background:var(--footer);color:#fff}
.footer-links{left:102px;top:17px;font-size:9.5px;word-spacing:3px}
.copyright{left:102px;top:37px;font-size:8px;color:#bbb}
</style>
</head>
<body>

<header class="site-header abs">
  <div class="brand abs"><span class="brand-mark"></span><span class="brand-name">HALVENRIDGE GROUP</span></div>
  <div class="utility abs">
    <span><svg viewBox="0 0 16 16"><rect x="3" y="7" width="10" height="8" rx="1" fill="#4a7fc1"/><path d="M5 7V5a3 3 0 0 1 6 0v2" stroke="#777" stroke-width="1.6" fill="none"/></svg>Login</span>
    <span><svg viewBox="0 0 16 16"><circle cx="6" cy="5" r="3" fill="#d9a066"/><rect x="2" y="9" width="8" height="6" rx="2" fill="#4a7fc1"/><circle cx="11" cy="6" r="2.5" fill="#d9a066"/></svg>Register</span>
    <span><svg viewBox="0 0 16 16"><circle cx="8" cy="5" r="3.2" fill="#d9a066"/><rect x="3" y="9" width="10" height="7" rx="2" fill="#7a3b22"/></svg>Live Support</span>
  </div>
  <div class="phone abs"><svg width="12" height="18" viewBox="0 0 12 18"><path d="M3 1l3 0 1 4-2 1c0 3 1 5 2 6l2-1 2 4-3 2C3 16 1 9 3 1z" fill="#222"/></svg>555-014-2870</div>
  <div class="search abs"><span class="search-field"></span><span class="search-btn">Search</span></div>
</header>

<nav class="main-nav abs">
  <a href="#">HOME</a><a href="#">SERVICES</a><a href="#">PROJECTS</a><a href="#">TEAM</a><a href="#">CONTACT US</a>
</nav>

<div class="hero abs" role="img" aria-label="Photo of a warm, wood-panelled hotel lounge with lamps and a fireplace"></div>
<h1 class="hero-title abs">NEW ERA OF DEVELOPMENT</h1>
<p class="hero-text abs">Lorem ipsum dolor sit amet consecteture adipiscing elit sed diam nonummy nibh euismod</p>
<div class="hero-dots abs"><span>1</span><span>2</span><span>3</span></div>

<main class="content-panel abs"></main>

<div class="section-tab welcome-tab abs"><span class="tab-icon"></span>WELCOME TO OUR COMPANY</div>
<div class="welcome-photo abs" role="img" aria-label="Photo of business people talking outdoors"></div>
<p class="welcome-text abs">Lorem ipsum dolor sit amet, consectetuer adipiscing elit, sed diam nonummy nibh euismod tincidunt ut laoreet dolore magna aliquam erat volutpat. Ut wisi enim ad minim veniam, quis nostrud exerci tation ullamcorper suscipit lobortis nisl ut aliquip ex ea commodo consequat. Duis autem vel eum iriure dolor in hendrerit in vulputate velit esse molestie consequat, vel illum dolore et iusto sollemnes in futurum.<br>odio dignissim qui blandit praesent luptatum zzril delenit augue duis dolore te feugait nulla facilisi. Nam liber tempor cum soluta nobis eleifend option congue nihil imperdiet doming id quod mazim placerat facer possim assum. Typi non habent claritatem insitam; est usus legentis in iis qui facit eorum claritatem. Investigationes demonstraverunt lectores legere me lius quod ii legunt saepius. Claritas est etiam processus dynamicus, qui sequitur mutationem consuetudium lectorum. Mirum est notare quam littera gothica, quam nunc putamus parum claram, anteposuerit litterarum formas . ii legunt saepius. Claritas est etiam processus dynamicus, qui sequitur mutationem consue-tudium lectorum. Mirum est notare quam littera gothica, quam nunc putamus parum claram, anteposuerit litterarum formas.<br><br><span class="read-more">Read more...</span></p>

<div class="section-tab side-tab abs" style="top:406px"><span class="tab-icon"></span>CREATING EXPERIENCES</div>
<p class="side-text abs" style="top:446px">Lorem ipsum dolor sit amet, con-sectetuer adipiscing elit, sed diam nonummy nibh euismod tincidunt ut laoreet dolore magna aliquam erat volutpat. Ut wisi enim ad minim veniam, <span class="read-more" style="margin-left:30px">Read more...</span></p>

<div class="section-tab side-tab abs" style="top:551px"><span class="tab-icon"></span>TESTIMONIAL</div>
<p class="side-text abs" style="top:590px">Lorem ipsum dolor sit amet, con-sectetuer adipiscing elit, sed diam nonummy in futurum.<br><span class="name">Marlowe 16Feb 2012</span><br>Lorem ipsum dolor sit amet, con-sectetuer adipiscing elit,<br><span class="name">Tessa 18Feb 2012</span> <span class="read-more" style="margin-left:20px">Read more...</span></p>

<div class="tab-row abs"><span class="active">SERVICES</span><span>BENEFITS</span><span>CAREERS</span><span>CONSULTING</span></div>
<div class="tab-box abs"></div>
<div class="tab-photo abs" role="img" aria-label="Photo of a smiling senior businessman with colleagues in a bright office"></div>
<ul class="service-list abs" style="left:115px;top:742px">
  <li>Hospiitality</li><li>Change Management</li><li>Application Management</li><li>People Managment</li><li>Datawarehousing</li><li class="plain">mordern Technologies</li><li>People Administration</li>
</ul>
<ul class="service-list abs" style="left:265px;top:741px">
  <li>We Offer Solutions</li><li>Conserve Process</li><li>Cleaning</li>
</ul>

<section class="abs" style="left:105px;top:985px;width:210px">
  <div class="col-head"><span class="tab-icon"></span>Current News</div>
  <p class="col-title" style="margin-top:22px">Lorem ipsum dolor sit amet, consectetuer adipiscing elit, sed diam</p>
  <p class="col-body">Tuesday, January 19th, 2010</p>
  <p class="col-body" style="margin-top:8px">Lorem ipsum dolor sit amet, consectetuer adipiscing eli.</p>
  <div class="more-btn" style="margin-top:6px">More</div>
</section>
<div class="col-rule abs" style="left:327px"></div>
<section class="abs" style="left:365px;top:985px;width:210px">
  <div class="col-head"><span class="tab-icon"></span>New Blogs</div>
  <p class="col-title" style="margin-top:22px">Tuesday, January 19th 2010</p>
  <p class="col-body" style="margin-top:4px">Lorem ipsum dolor sit amet, consectetuer adipiscing elit, sed diam</p>
  <p class="col-body" style="margin-top:6px">Lorem ipsum dolor sit amet, consectetuer adipiscing eli.</p>
  <div class="more-btn" style="margin-top:6px">More</div>
</section>
<div class="col-rule abs" style="left:602px"></div>
<div class="col-head abs" style="left:635px;top:985px"><span class="tab-icon"></span>Follow Us</div>
<div class="social abs" aria-label="Social profiles"><span></span><span></span><span></span><span></span></div>
<div class="footer-brand abs"><span class="brand-mark"></span><span class="brand-name">HALVENRIDGE GROUP</span></div>

<footer class="site-footer abs">
  <p class="footer-links abs">link1 | link2 | link3 | link4 | link5 | link6 | link7 | link8</p>
  <p class="copyright abs">© 2012. All Rights Reserved</p>
</footer>

</body>
</html>
```